Trendy eye catching business card for lawn mowing business

Turf Tidy, a local community lawn mowing service, requires an eye catching trendy business card to drop into letterboxes.

We could simply throw something together from a Microsoft Word template, but we are wanting something more than this. Some other business’ images are attached for some inspiration.

We are requiring the card to have Turf Tidy with our slogan, Call The Brindles. In addition, provide details with that we are a local, affordable lawn mowing service, and for other gardening matters to simply just ask!
Plus the relevant contact details, phone, email, social media.

Target Market(s)

Local community members who require assistance with their garden care

Industry/Entity Type

Gardening

Contact Information for Business Card

the name TURF TIDY is our logo
telephone logo 0438 215 967
email logo turftidy@postbox-mail.example
Instagram logo turftidy
Facebook logo turftidy.sth
Lawn Mowing Service
Local Affordable
edge trim, blow and clipping removal included.
Other gardening matters, just ask!

Font styles to use
Serif
Sans Serif
Decorative
Script

Colors
9bcb3c
ffffff

Requirements
Must have
• All the details listed in Business Card Details.
Make these words prominent:
Turf Tidy
Lawn Mowing Service
Local
Affordable
Nice to have
• Our slogan ‘Call The Brindles’ incorporated.
Different colour background for front and reverse side
Greens, white and black colours
Subtle grass blades images incorporated
Should not have
• No images of lawnmowers.
No images of men/cartoons.
No using initials for Turf Tidy

```html
<!DOCTYPE html>
<html lang="en">
<head>
<meta charset="utf-8">
<title>Turf Tidy – Business Card</title>
<link rel="stylesheet" href="https://fonts.googleapis.com/css2?family=Anton&family=Roboto:wght@400;500;700&family=Exo+2:wght@300&display=swap">
<style>
  :root {
    --page-bg: #d6d6d6;
    --card-white: #ffffff;
    --lawn-green: #84bc45;
    --lawn-green-dark: #6fa534;
    --blade-green: #8cc63f;
    --ink: #1a1a1a;
    --slogan-grey: #555555;
  }
  * { margin: 0; padding: 0; box-sizing: border-box; }
  html, body {
    width: 1200px;
    height: 802px;
    overflow: hidden;
    background: var(--page-bg);
  }
  .sheet {
    position: relative;
    width: 1200px;
    height: 802px;
  }
  .card {
    position: absolute;
    top: 241px;
    width: 540px;
    height: 320px;
    overflow: hidden;
  }

  /* Front */
  .card-front {
    left: 40px;
    background: var(--card-white);
  }
  .brand-name {
    position: absolute;
    left: 33px;
    top: 50px;
    font-family: "Anton", sans-serif;
    font-size: 52px;
    line-height: 1;
    color: var(--ink);
    letter-spacing: 0.5px;
  }
  .slogan {
    position: absolute;
    left: 33px;
    top: 111px;
    width: 324px;
    display: flex;
    align-items: center;
    gap: 8px;
    font-family: "Roboto", sans-serif;
    font-weight: 700;
    font-size: 19px;
    letter-spacing: 2.4px;
    color: var(--slogan-grey);
    white-space: nowrap;
  }
  .slogan::before, .slogan::after {
    content: "";
    flex: 1;
    height: 2px;
    background: var(--slogan-grey);
  }
  .contact-list {
    position: absolute;
    left: 35px;
    list-style: none;
    font-family: "Roboto", sans-serif;
    font-size: 15px;
    color: var(--ink);
  }
  .contact-list li {
    display: flex;
    align-items: center;
    gap: 7px;
    height: 20px;
  }
  .contact-direct { top: 186px; }
  .contact-social { top: 256px; }
  .icon { width: 16px; height: 16px; flex: none; }
  .social-dot {
    width: 14px;
    height: 14px;
    border-radius: 50%;
    border: 1.5px solid var(--lawn-green);
    flex: none;
    margin: 0 1px;
  }
  .grass-art-front {
    position: absolute;
    left: 372px;
    top: 18px;
    width: 160px;
    height: 296px;
    background: linear-gradient(to top, rgba(140,198,63,0.55), rgba(140,198,63,0.08));
  }
  .front-band {
    position: absolute;
    left: 0;
    bottom: 0;
    width: 100%;
    height: 10px;
    background: var(--lawn-green);
  }

  /* Back */
  .card-back {
    left: 620px;
    background: var(--lawn-green);
    color: var(--card-white);
    text-align: center;
  }
  .grass-art-left, .grass-art-right, .grass-art-strip {
    position: absolute;
  }
  .grass-art-left {
    left: 0; top: 10px; width: 115px; height: 310px;
    background: linear-gradient(to top, rgba(90,150,40,0.55), rgba(90,150,40,0));
  }
  .grass-art-right {
    right: 0; top: 10px; width: 130px; height: 310px;
    background: linear-gradient(to top, rgba(90,150,40,0.55), rgba(90,150,40,0));
  }
  .grass-art-strip {
    left: 115px; bottom: 0; width: 295px; height: 50px;
    background: linear-gradient(to top, rgba(90,150,40,0.45), rgba(90,150,40,0));
  }
  .back-copy {
    position: absolute;
    left: 0;
    top: 98px;
    width: 100%;
    font-family: "Roboto", sans-serif;
  }
  .service-title {
    font-weight: 700;
    font-size: 27px;
    line-height: 32px;
    letter-spacing: 0.4px;
  }
  .service-tagline {
    font-weight: 400;
    font-size: 23px;
    line-height: 30px;
  }
  .service-details {
    margin-top: 24px;
    font-size: 17.5px;
    line-height: 23px;
  }
  .service-phone {
    margin-top: 2px;
    font-family: "Exo 2", sans-serif;
    font-weight: 300;
    font-size: 24px;
    letter-spacing: 2px;
  }
</style>
</head>
<body>
<main class="sheet">

  <section class="card card-front" aria-label="Business card front">
    <h1 class="brand-name">TURF TIDY</h1>
    <p class="slogan">CALL THE BRINDLES</p>

    <ul class="contact-list contact-direct">
      <li>
        <svg class="icon" viewBox="0 0 16 16" aria-hidden="true">
          <rect x="1" y="1" width="14" height="14" rx="2" fill="none" stroke="#84bc45" stroke-width="1.5"/>
          <path d="M5 4.2c.6-.4 1.1-.2 1.4.4l.6 1.2c.2.4.1.8-.3 1.1l-.4.3c.5 1.1 1.3 1.9 2.4 2.4l.3-.4c.3-.4.7-.5 1.1-.3l1.2.6c.6.3.8.8.4 1.4-.5.8-1.3 1.2-2.2.9C7.2 11 5 8.8 4.2 6.4 3.9 5.5 4.2 4.7 5 4.2z" fill="#84bc45"/>
        </svg>
        <span>0438 215 967</span>
      </li>
      <li>
        <svg class="icon" viewBox="0 0 16 16" aria-hidden="true">
          <rect x="1" y="3" width="14" height="10" fill="#84bc45"/>
          <path d="M1 3l7 5.5L15 3" fill="none" stroke="#ffffff" stroke-width="1.3"/>
        </svg>
        <span>turftidy@postbox-mail.example</span>
      </li>
    </ul>

    <ul class="contact-list contact-social">
      <li><span class="social-dot" aria-hidden="true"></span><span>photos.example/turftidy</span></li>
      <li><span class="social-dot" aria-hidden="true"></span><span>social.example/turftidy.sth</span></li>
    </ul>

    <div class="grass-art-front" role="img" aria-label="Illustration of tall green grass blades"></div>
    <div class="front-band"></div>
  </section>

  <section class="card card-back" aria-label="Business card back">
    <div class="grass-art-left" role="img" aria-label="Faint darker green grass blades rising from the left edge"></div>
    <div class="grass-art-right" role="img" aria-label="Faint darker green grass blades rising from the right edge"></div>
    <div class="grass-art-strip" role="img" aria-label="Row of short faint grass tufts along the bottom"></div>

    <div class="back-copy">
      <h2 class="service-title">LAWN MOWING SERVICE</h2>
      <p class="service-tagline">Local. Affordable.</p>
      <p class="service-details">Edge trim, blow and clipping removal included.<br>Other gardening matters, just ask!</p>
      <p class="service-phone">0438 215 967</p>
    </div>
  </section>

</main>
</body>
</html>
```